Stylish business cards for KV7

To create an appealing and professional business card design for a WOMEN Owned Construction Supply Company.
2 sided card. Incorporate brand elements, curvy, colorful, sleek and bright. No solid white background. attached samples of styles added shapes/ribbons. Want something with that WOW that looks awesome, factor. It is a new logo, so feel free to mess with logo colors in the blue and teal factors that can look good with both dark and light background. If you want to try a watermark with just the KV7, without the "Supply" that might look cool to.

Industry/Entity Type

Women owned construction supply company

Contact Information for Business Card

Name, Title, and phone number and email, web page. maybe spot for qr code.

Font styles to use
Sans Serif

Requirements
Nice to have
• would love to see colors, maybe stylish ribbon dividers or some sort of 2 or 3 tone color card that compliments logo.
Should not have
• Please do not have all white background. Do not include Home/reale state/ or building images.

```html
<!DOCTYPE html>
<html lang="en">
<head>
<meta charset="utf-8">
<title>KV7 Supply – Business Card</title>
<link rel="stylesheet" href="https://fonts.googleapis.com/css2?family=Montserrat:wght@400;500;800&display=swap">
<style>
  :root {
    --backdrop: #3a3b3e;
    --navy: #112a4a;
    --navy-deep: #0d2240;
    --navy-emboss: #1b3a63;
    --teal: #1e9bc9;
    --white: #ffffff;
  }
  * { margin: 0; padding: 0; box-sizing: border-box; }
  html, body {
    width: 1200px; height: 1200px; overflow: hidden;
    background: var(--backdrop);
    font-family: "Montserrat", sans-serif;
  }
  .sheet {
    position: relative; width: 1200px; height: 1200px;
    display: flex; flex-direction: column; align-items: center; justify-content: center; gap: 60px;
  }
  .card {
    position: relative; width: 900px; height: 514px;
    border-radius: 40px; overflow: hidden;
    border: 3px solid var(--teal);
  }
  .card-shapes { position: absolute; inset: 0; width: 100%; height: 100%; }

  .contact-block {
    position: absolute; left: 80px; top: 190px; color: var(--white);
  }
  .full-name {
    font-weight: 800; font-size: 44px; color: var(--teal); letter-spacing: 1px; line-height: 1;
  }
  .job-title {
    font-weight: 500; font-size: 24px; margin-top: 8px; letter-spacing: 1px;
  }
  .contact-list { list-style: none; margin-top: 22px; }
  .contact-list li {
    display: flex; align-items: center; gap: 16px;
    font-size: 24px; font-weight: 400; margin-bottom: 12px; letter-spacing: 0.5px;
  }
  .contact-icon { width: 28px; height: 28px; flex: none; }

  .brand-name {
    position: absolute; font-weight: 800; letter-spacing: 1px; white-space: nowrap; line-height: 1;
  }
  .brand-front { left: 560px; top: 175px; font-size: 50px; color: var(--navy); }

  .card-back { background: linear-gradient(180deg, var(--navy) 0%, var(--navy-deep) 100%); }
  .brand-back {
    left: 50%; top: 42%; transform: translate(-50%, -50%);
    font-size: 44px; color: var(--white);
  }
  .watermark {
    position: absolute; font-weight: 800; font-size: 40px; line-height: 1;
    color: var(--navy-emboss); letter-spacing: 1px;
  }
</style>
</head>
<body>
<main class="sheet">

  <section class="card card-front" aria-label="Card front">
    <svg class="card-shapes" viewBox="0 0 900 514" preserveAspectRatio="none" aria-hidden="true">
      <defs>
        <linearGradient id="paper" x1="0" y1="0" x2="0" y2="1">
          <stop offset="0" stop-color="#ffffff"/>
          <stop offset="1" stop-color="#e4e5e7"/>
        </linearGradient>
      </defs>
      <rect width="900" height="514" fill="url(#paper)"/>
      <path d="M0,0 H325 C420,25 445,190 475,300 C505,420 560,495 650,514 H0 Z" fill="#1e9bc9"/>
      <path d="M0,0 H300 C395,25 420,195 450,305 C480,425 535,500 615,514 H0 Z" fill="#112a4a"/>
      <path d="M300,0 C402,25 428,192 459,302 C490,422 545,498 630,514" fill="none" stroke="#ffffff" stroke-width="4"/>
    </svg>

    <div class="contact-block">
      <p class="full-name">FULL NAME</p>
      <p class="job-title">TITLE</p>
      <ul class="contact-list">
        <li>
          <svg class="contact-icon" viewBox="0 0 24 24" aria-hidden="true"><path fill="#1e9bc9" d="M6.6 10.8a15.1 15.1 0 0 0 6.6 6.6l2.2-2.2a1 1 0 0 1 1-.25 11.4 11.4 0 0 0 3.6.57 1 1 0 0 1 1 1V20a1 1 0 0 1-1 1A17 17 0 0 1 3 4a1 1 0 0 1 1-1h3.5a1 1 0 0 1 1 1c0 1.25.2 2.45.57 3.57a1 1 0 0 1-.25 1z"/></svg>
          (000) 000 0000
        </li>
        <li>
          <svg class="contact-icon" viewBox="0 0 24 24" aria-hidden="true"><rect x="2" y="5" width="20" height="14" fill="#1e9bc9"/><path d="M2 5l10 8 10-8" fill="none" stroke="#112a4a" stroke-width="2"/></svg>
          email@company.com
        </li>
        <li>
          <svg class="contact-icon" viewBox="0 0 24 24" aria-hidden="true"><g fill="none" stroke="#1e9bc9" stroke-width="2"><circle cx="12" cy="12" r="10"/><ellipse cx="12" cy="12" rx="4.5" ry="10"/><path d="M2 12h20M4 7h16M4 17h16"/></g></svg>
          www.company.com
        </li>
      </ul>
    </div>

    <p class="brand-name brand-front">KV7 Supply</p>
  </section>

  <section class="card card-back" aria-label="Card back">
    <div class="watermark-field" aria-hidden="true">
      <span class="watermark" style="left:330px; top:40px;">KV7</span>
      <span class="watermark" style="left:620px; top:50px;">KV7</span>
      <span class="watermark" style="left:130px; top:120px;">KV7</span>
      <span class="watermark" style="left:740px; top:160px;">KV7</span>
      <span class="watermark" style="left:50px; top:250px;">KV7</span>
      <span class="watermark" style="left:290px; top:300px;">KV7</span>
      <span class="watermark" style="left:560px; top:290px;">KV7</span>
      <span class="watermark" style="left:780px; top:330px;">KV7</span>
      <span class="watermark" style="left:140px; top:400px;">KV7</span>
      <span class="watermark" style="left:430px; top:420px;">KV7</span>
      <span class="watermark" style="left:660px; top:430px;">KV7</span>
    </div>
    <p class="brand-name brand-back">KV7 Supply</p>
  </section>

</main>
</body>
</html>
```